Exclusive beauty salon needs a price list or services booklet

I need a new very attractive flyer for my beauty salon, containing information on the different services and their prices.
In attachment you can find a pdf of the "old" one, but I'd love to have a beautifully designed new one!
I'd love to have a booklet in format 148 x 148 mm, or in US format, containing 12 or 16 pages, but if you can offer other nice looking designs they are welcome!
The services that need to come in the booklet with their prices can all be found on my website: www.atelierverano.be, starting with
Gelaatsverzorging
Wimperverlenging
Suikerontharing
Wimperlifting
Permanente Make Up
Airbrush Tanning

Target Market(s)

woman from 20 to 89 years old

Industry/Entity Type

Beauty Salon

Font styles to use
Sans Serif

Colors

Designer to choose colors to be used in the design.

Requirements
Must have
• a classy nice look, it must contain details about the services from my beauty salon and their prices, and nice pictures.
• The Names, prices and explanations of the services can easily be found on my website: www.atelierverano.be
Nice to have
• In attachment you can find the "old" price list in pdf, what I need now is a "new booklet" with the new logo and updated services price list.
• I need a very nice and attractive looking booklet, classy chique, Paris chique, looking very expensive.
Should not have
• Not too much colors, not too curly, but still feminine

```html
<!DOCTYPE html>
<html lang="nl">
<head>
<meta charset="utf-8">
<title>Airbrush Tanning – Atelier Verano</title>
<link href="https://fonts.googleapis.com/css2?family=Lora:wght@400;500&family=Didact+Gothic&display=swap" rel="stylesheet">
<style>
  :root {
    --backdrop: #e4e4e4;
    --paper: #ffffff;
    --paper-shade: #f3f3f3;
    --ink: #2b2b2b;
    --body-ink: #4a4a4a;
    --teal: #7fc9c4;
    --teal-soft: #a8dcd7;
    --rule: #9fd3cf;
  }
  * { box-sizing: border-box; margin: 0; padding: 0; }
  html, body { width: 1200px; height: 900px; overflow: hidden; }
  body {
    background: var(--backdrop);
    font-family: "Didact Gothic", "Century Gothic", sans-serif;
    color: var(--body-ink);
  }
  .spread {
    position: absolute;
    left: 100px; top: 200px;
    width: 1000px; height: 500px;
    display: flex;
  }
  .page {
    position: relative;
    width: 500px; height: 500px;
    background: var(--paper);
    overflow: hidden;
  }
  .page--left { background: linear-gradient(90deg, var(--paper) 80%, var(--paper-shade)); }
  .page--right { background: linear-gradient(90deg, var(--paper-shade), var(--paper) 12%); }

  .page-title {
    position: absolute; top: 26px; left: 40px; right: 0;
    text-align: center;
    font-family: "Lora", Georgia, serif;
    font-weight: 400; font-size: 25px; color: var(--ink);
  }
  .title-rule {
    position: absolute; top: 66px; left: 250px;
    width: 32px; height: 2px; background: var(--rule);
  }
  .intro {
    position: absolute; top: 80px; left: 52px; right: 28px;
    text-align: center; font-size: 13px; line-height: 1.7; color: var(--ink);
  }
  .portrait {
    position: absolute; left: 0; top: 142px; width: 242px; height: 358px;
    background: radial-gradient(ellipse at 50% 30%, #f2d3c5 0%, #d9a98f 45%, #6b4a3a 75%, #f4f1f1 100%);
  }
  .flowers {
    position: absolute; right: 0; top: 288px; width: 248px; height: 212px;
    background: radial-gradient(ellipse at 60% 55%, #fbf3ef 0%, #f2cfd8 40%, #d9e6cf 70%, rgba(255,255,255,0) 92%);
  }
  .section-heading {
    font-family: "Lora", Georgia, serif;
    font-weight: 500; font-size: 15px; color: var(--teal);
    margin-bottom: 10px;
  }
  .body-text {
    font-size: 7.6px; line-height: 1.85; text-align: justify; color: var(--body-ink);
  }
  .body-text p + p { margin-top: 0; }
  .col { position: absolute; }
  .col--left-intro { left: 246px; top: 192px; width: 226px; }
  .col--right-a { left: 42px; top: 72px; width: 200px; }
  .col--right-b { left: 262px; top: 72px; width: 208px; }
  .col--right-a .section-heading.lower { margin-top: 14px; }

  .price-band {
    position: absolute; top: 0; left: 0; right: 0; height: 52px;
    background: linear-gradient(90deg, var(--teal-soft), var(--teal), var(--teal-soft));
    text-align: center; color: #fff;
    font-family: "Lora", Georgia, serif; font-size: 14px; line-height: 1.15;
    padding-top: 10px;
  }
  .folio {
    position: absolute; left: 46px; bottom: 14px;
    display: flex; align-items: center; gap: 8px;
    font-size: 11px; color: #fff;
  }
  .folio-number {
    width: 22px; height: 22px; background: var(--teal);
    display: flex; align-items: center; justify-content: center;
    font-size: 12px;
  }
  .folio-label { color: var(--ink); opacity: .55; }
  .footer-rule {
    position: absolute; left: 246px; right: 28px; top: 466px;
    height: 1px; background: #e4e4e4;
  }
</style>
</head>
<body>
<main class="spread">
  <section class="page page--left">
    <h1 class="page-title">Airbrush Tanning</h1>
    <div class="title-rule"></div>
    <p class="intro">Altijd al gedroomd van een natuurlijk mooi én egaal bruin kleurtje? En dit zonder te puffen in de zon of te knoeien met zelfbruiner? Ik stel u graag de spraycabine van Atelier Verano voor!</p>
    <div class="portrait" role="img" aria-label="Portretfoto van een vrouw met een krans van roze rozen in het haar"></div>
    <div class="col col--left-intro">
      <h2 class="section-heading">De Voorbereiding</h2>
      <div class="body-text">
        <p>De dag van de afspraak kan je beter geen vette of oliehoudende producten op het lichaam aanbrengen. Een goede scrubbeurt (op waterbasis, zonder olie !!) zal ervoor zorgen dat de kleur mooi egaal en gelijkmatig verdeeld wordt en belangrijker nog, dat je huid veel langer bruin zal blijven. De loszittende dode huidcellen worden verwijderd bij het scrubben. Degene die nog vast zitten zullen nog veel langer op hun plaats blijven. Opgelet : indien je zelf de scrub uitvoert, zorg ervoor dat je geen stukken vergeet !</p>
        <p>Trek donkere loszittende kledij aan. Op lichte kledij kan de geleurde component licht kleur afgeven. Dit laat zich volledig verwijderen in de was. De kledij mag niet spannen en vooral geen wrijving op de huid geven.</p>
      </div>
    </div>
    <div class="footer-rule"></div>
    <div class="folio"><span class="folio-number">6</span><span class="folio-label">Airbrush Tanning</span></div>
  </section>

  <section class="page page--right">
    <header class="price-band">airbrush tanning van het volledige lichaam<br>€29</header>
    <div class="col col--right-a body-text">
      <p>De component die de uiteindelijke kleur moet geven werkt gedurende ongeveer 12 uur verder. Op plaatsen waar de kledij op de huid schuurt kan het product voortijdig weggewreven worden en dus lichtere strepen geven.</p>
      <p>Het product laat geen vlekken na op de kledij. Alleen op de materialen van zeer fijne lingerie kan het het eventueel inwerken.</p>
      <p>Het product werkt heel goed in op nagels (is een verhoorning van de huid en bestaat dus ook uit dode keratine huidcellen) ! Wij proberen deze zo veel mogelijk te sparen bij het spuiten. Om helemaal zeker te zijn, vooral bij veelvuldige herhalingen, kan je beter je nagels lakken, eventueel met een kleurloze nagellak. Let wel op dat je geen huid bedekt met de lak.</p>
      <h2 class="section-heading lower">De Voorbereiding</h2>
      <p>Je huid wordt ingespoten met het product. Je ziet onmiddellijk het resultaat. Eventueel wordt in verschillende lagen gespoten zodat je zeker niet te bruin kan worden. Het inspuiten van het volledig lichaam duurt ongeveer 10 minuten. Daarna moet je drogen voor je de kleren aan te trekken nog een kwartiertje het product laten indrogen. Je verlaat het instituut met een mooie, gezonde bruine kleur.</p>
    </div>
    <div class="col col--right-b">
      <h2 class="section-heading">De Nazorg</h2>
      <div class="body-text">
        <p>Gedurende de eerste 8 uren na de airbrush tanning kan je best vermijden om hevig te zweten. Dus best geen sport of andere zware inspanningen. Je mag niet douchen ! Tijdens deze eerste 8 uren kan het product een lichte kleur afgeven op kledij of lakens. Deze verdwijnt zonder probleem in de was. Na 8 uur mag je douchen. De tijdelijke kleurcomponent spoelt volledig weg. Ondertussen heeft je huid een mooie bruine kleur gekregen. Hoe beter je je huid hydrateert hoe langer je de kleur kan behouden. Je kleur blijft gemiddeld tussen de 7 dagen en 10 dagen naargelang je huidtype. Daarna begint de kleur te vervagen.</p>
      </div>
    </div>
    <div class="flowers" role="img" aria-label="Foto van witte orchideeën en lichtroze rozen"></div>
  </section>
</main>
</body>
</html>
```